HearthMile business card and stationary design

We are looking for a simple yet elegant design for our mortgage company business card and stationary.

The card should include:
Name (Marcus Pell)
Title (CEO)
Phone Number (732-555-0182)
Address (48 Birchwell Court, Suite 314, Brookhollow, NJ 07791)
Email (email@hearthmile.example)
"NMLS" i.e. (NMLS 61947)
"Company NMLS" (Company NMLS 274615)

Contact Information for Business Card

See above

```html
<!DOCTYPE html>
<html lang="en">
<head>
<meta charset="utf-8">
<title>HearthMile Business Card</title>
<link rel="stylesheet" href="https://fonts.googleapis.com/css2?family=Montserrat:wght@600;700&family=Arimo:wght@400&display=swap">
<style>
  :root {
    --page-bg: #0d0d0e;
    --card-bg: #262729;
    --card-back-bg: #232426;
    --accent-blue: #12a4e6;
    --text-white: #f4f5f6;
    --emboss-grey: #5c5d60;
  }
  * { box-sizing: border-box; margin: 0; padding: 0; }
  html, body { width: 1200px; height: 820px; overflow: hidden; background: var(--page-bg); }
  .canvas { position: relative; width: 1200px; height: 820px; }

  .card {
    position: absolute;
    width: 620px;
    height: 354px;
    border-left: 3px solid var(--accent-blue);
    border-bottom: 3px solid var(--accent-blue);
  }
  .card-front { left: 50px; top: 50px; background: var(--card-bg); }
  .card-back  { left: 530px; top: 420px; background: var(--card-back-bg); }

  .brand-name {
    position: absolute;
    font-family: "Montserrat", sans-serif;
    font-weight: 600;
    letter-spacing: 0.5px;
    white-space: nowrap;
  }
  .card-front .brand-name { left: 230px; top: 52px; font-size: 54px; color: var(--text-white); }
  .card-back .brand-name {
    left: 0; right: 0; top: 140px; text-align: center;
    font-size: 58px; color: var(--emboss-grey);
  }

  .divider {
    position: absolute; left: 88px; right: 84px; top: 158px;
    height: 1px; background: var(--accent-blue);
  }

  .person { position: absolute; left: 96px; top: 170px; }
  .person-name {
    font-family: "Montserrat", sans-serif; font-weight: 700;
    font-size: 29px; color: var(--accent-blue); line-height: 1.05;
  }
  .person-title {
    font-family: "Arimo", sans-serif; font-size: 20px;
    color: var(--text-white); margin-left: 10px; line-height: 1.2;
  }

  .contact-list { list-style: none; position: absolute; left: 108px; top: 262px; }
  .contact-list li {
    display: flex; align-items: center; gap: 8px;
    font-family: "Arimo", sans-serif; font-size: 18px;
    color: var(--text-white); line-height: 27px;
    white-space: nowrap;
  }
  .contact-list svg { width: 16px; height: 16px; flex: none; }
  .contact-list .accent { color: var(--accent-blue); }

  .licence {
    position: absolute; right: 84px; top: 170px; text-align: right;
    font-family: "Arimo", sans-serif; font-size: 18px; line-height: 24px;
    color: var(--text-white); white-space: nowrap;
  }
  .licence .label { color: var(--accent-blue); }

  .address {
    position: absolute; right: 70px; top: 226px; text-align: right;
    font-family: "Arimo", sans-serif; font-style: normal;
    font-size: 18px; line-height: 24px;
    color: var(--text-white); white-space: nowrap;
  }
</style>
</head>
<body>
<main class="canvas">

  <section class="card card-front" aria-label="Business card front">
    <div class="brand-name">HearthMile</div>
    <div class="divider"></div>

    <div class="person">
      <div class="person-name">Marcus Pell</div>
      <div class="person-title">CEO</div>
    </div>

    <div class="licence">
      <div><span class="label">NMLS</span> 61947</div>
      <div><span class="label">Company NMLS</span> 274615</div>
    </div>

    <address class="address">
      <div>48 Birchwell Court, Suite 314</div>
      <div>Brookhollow, NJ 07791</div>
    </address>

    <ul class="contact-list">
      <li>
        <svg viewBox="0 0 24 24" aria-hidden="true"><path fill="#12a4e6" d="M6.6 10.8a15.1 15.1 0 0 0 6.6 6.6l2.2-2.2c.3-.3.7-.4 1-.2 1.1.4 2.3.6 3.6.6.6 0 1 .4 1 1V20c0 .6-.4 1-1 1A17 17 0 0 1 3 4c0-.6.4-1 1-1h3.5c.6 0 1 .4 1 1 0 1.3.2 2.5.6 3.6.1.3 0 .7-.2 1z"/></svg>
        <span>732-555-0182</span>
      </li>
      <li>
        <svg viewBox="0 0 24 24" aria-hidden="true"><rect x="2" y="5" width="20" height="14" fill="#12a4e6"/><path d="M2 5l10 8 10-8" fill="none" stroke="#262729" stroke-width="1.6"/></svg>
        <span>email@hearthmile.example</span>
      </li>
      <li>
        <svg viewBox="0 0 24 24" aria-hidden="true"><g fill="none" stroke="#12a4e6" stroke-width="1.8"><circle cx="12" cy="12" r="9.5"/><ellipse cx="12" cy="12" rx="4.2" ry="9.5"/><path d="M2.5 12h19M4 7h16M4 17h16"/></g></svg>
        <span>www.<span class="accent">hearthmile</span>.example</span>
      </li>
    </ul>
  </section>

  <section class="card card-back" aria-label="Business card back">
    <div class="brand-name">HearthMile</div>
  </section>

</main>
</body>
</html>
```